Business Card Design - Photographer

I am a landscape photographer and I require a business card design. 

I require two designs:
1)  a double sided business card
 and
b)  a single sided business card 

The single sided design can either be the same as the double sided (with just one side having all the information)....or it can be an entire new design. Its up to you.

My corporate colours are (CMYK):

Blue   69, 32, 0, 0
Grey  72,  64,  47,  31
Green  32,  2,  91,  0
Yellow   0, 19, 92, 0
Orange  0, 39, 75, 0

Colour space in final file should be in CMYK.

The details that need to be included on the card:

- Use the provided Logo
- Name: Wiktor Baranowski
- Email:   sales@vistalumeworks.com.au
- Website:    vistalumeworks.com.au
- Twitter:    quipline.com/vistalumeworks
- Facebook:   gatherly.com/vistalumeworks
- Mobile  0417 539 662

Please use the attached template to design the logo to the specified size, including the marked bleed lines. I have also attached my logo in PNG (transparent background) and ai format for you to use.

The final file should be:
- Photoshop version with layers so I can edit the name/text etc. All non vector files should be high resolution at 1039 x 697 pixels at 300 dpi.

I also require a file as:
- Vector based PDF

Anyway questions please contact me.

Thank you

Industry/Entity Type

Landscape

Logo styles of interest
Pictorial/Combination Logo
Abstract Logo
Wordmark Logo
Lettermark Logo
Requirements
Must have
• The details that need to be included on the card:

- Use the provided Logo
- Name: Wiktor Baranowski
- Email: sales@vistalumeworks.com.au
- Website: vistalumeworks.com.au
- Twitter: quipline.com/vistalumeworks
- Facebook: gatherly.com/vistalumeworks
- Mobile 0417 539 662

```html
<!DOCTYPE html>
<html lang="en">
<head>
<meta charset="utf-8">
<title>Vistalume Works – Business Card</title>
<link rel="stylesheet" href="https://fonts.googleapis.com/css2?family=Cinzel:wght@500&family=Jura:wght@600&family=Source+Sans+3:wght@400&display=swap">
<style>
  :root {
    --page-grey: #c9c9c9;
    --card-white: #ffffff;
    --trim-dash: #9a9a9a;
    --frame-green: #a6ce39;
    --brand-slate: #434152;
    --brand-orange: #f5a347;
    --watermark-grey: #dcdce0;
    --text-dark: #3a3a44;
  }
  * { margin: 0; padding: 0; box-sizing: border-box; }
  html, body { width: 1200px; height: 817px; overflow: hidden; background: var(--page-grey); }
  .canvas { position: relative; width: 1200px; height: 817px; overflow: hidden; }

  .bleed-card {
    position: absolute; left: 50px; top: 50px; width: 1103px; height: 727px;
    background: var(--card-white); border: 1.5px dashed var(--trim-dash);
  }
  .safe-frame {
    position: absolute; left: 78px; top: 78px; width: 1050px; height: 675px;
    border: 2px solid var(--frame-green);
  }
  .header-band {
    position: absolute; left: 79px; top: 79px; width: 1048px; height: 190px;
    background: var(--brand-slate);
  }
  .brand-mark {
    position: absolute; left: 82px; top: 79px; width: 190px; height: 190px;
  }
  .brand-name {
    position: absolute; left: 347px; top: 118px; width: 692px; text-align: center;
    font-family: "Cinzel", serif; font-weight: 500; font-size: 58px; line-height: 1;
    letter-spacing: 2px; color: var(--brand-orange);
  }
  .brand-rule {
    position: absolute; left: 347px; top: 184px; width: 692px; height: 2px;
    background: var(--brand-orange);
  }
  .brand-tagline {
    position: absolute; left: 347px; top: 204px; width: 692px; text-align: center;
    font-family: "Cinzel", serif; font-weight: 500; font-size: 26px; line-height: 1;
    letter-spacing: 4px; color: var(--brand-orange);
  }

  .watermark {
    position: absolute; left: 640px; top: 270px; width: 480px; height: 470px;
  }

  .person-name {
    position: absolute; left: 200px; top: 306px; width: 900px; text-align: center;
    font-family: "Jura", sans-serif; font-weight: 600; font-size: 64px; line-height: 1;
    letter-spacing: 2px; color: var(--brand-orange);
    -webkit-text-stroke: 1.5px var(--brand-slate);
  }

  .contact-list { position: absolute; left: 94px; top: 464px; list-style: none; }
  .contact-item {
    display: flex; align-items: center; height: 46px;
    font-family: "Source Sans 3", sans-serif; font-size: 45px; line-height: 1; color: var(--text-dark);
  }
  .contact-item:first-child { height: 58px; margin-bottom: 8px; }
  .contact-icon { flex: none; margin-right: 8px; }
</style>
</head>
<body>
<div class="canvas">
  <div class="bleed-card"></div>
  <div class="safe-frame"></div>

  <svg class="watermark" viewBox="0 0 480 470" role="img" aria-label="Faint brand symbol watermark">
    <circle cx="240" cy="232" r="228" fill="var(--watermark-grey)" opacity="0.7"/>
  </svg>

  <div class="header-band"></div>
  <svg class="brand-mark" viewBox="0 0 190 190" role="img" aria-label="Brand symbol placeholder">
    <circle cx="95" cy="95" r="86" fill="var(--card-white)"/>
  </svg>
  <div class="brand-name">VISTALUME WORKS</div>
  <div class="brand-rule"></div>
  <div class="brand-tagline">FINE ART PHOTOGRAPHY</div>

  <h1 class="person-name">Wiktor Baranowski</h1>

  <ul class="contact-list">
    <li class="contact-item">
      <svg class="contact-icon" width="46" height="46" viewBox="0 0 46 46"><circle cx="23" cy="23" r="21" fill="var(--brand-slate)"/></svg>
      vistalumeworks.com.au
    </li>
    <li class="contact-item">
      <svg class="contact-icon" width="24" height="38" viewBox="0 0 24 38">
        <rect x="1" y="1" width="22" height="36" rx="3" fill="var(--brand-slate)"/>
        <rect x="5" y="5" width="14" height="10" fill="var(--card-white)"/>
        <g fill="var(--card-white)">
          <rect x="5" y="19" width="3" height="3"/><rect x="10.5" y="19" width="3" height="3"/><rect x="16" y="19" width="3" height="3"/>
          <rect x="5" y="25" width="3" height="3"/><rect x="10.5" y="25" width="3" height="3"/><rect x="16" y="25" width="3" height="3"/>
          <rect x="5" y="31" width="3" height="3"/><rect x="10.5" y="31" width="3" height="3"/><rect x="16" y="31" width="3" height="3"/>
        </g>
      </svg>
      0417 539 662
    </li>
    <li class="contact-item">
      <svg class="contact-icon" width="40" height="28" viewBox="0 0 40 28" style="margin-right:2px">
        <rect x="1.5" y="1.5" width="37" height="25" fill="none" stroke="var(--brand-slate)" stroke-width="3"/>
        <path d="M2 2 L20 16 L38 2 M2 26 L15 12 M38 26 L25 12" fill="none" stroke="var(--brand-slate)" stroke-width="3"/>
      </svg>
      sales@vistalumeworks.com.au
    </li>
    <li class="contact-item">
      <svg class="contact-icon" width="30" height="30" viewBox="0 0 30 30"><rect width="30" height="30" rx="3" fill="var(--brand-slate)"/></svg>
      gatherly.com/vistalumeworks
    </li>
    <li class="contact-item">
      <svg class="contact-icon" width="30" height="30" viewBox="0 0 30 30"><rect width="30" height="30" rx="3" fill="var(--brand-slate)"/></svg>
      quipline.com/vistalumeworks
    </li>
  </ul>
</div>
</body>
</html>
```